Quorva - corporate Business Card

We need a good look and innovative business card for a new start up company based in Los Angeles called "Quorva". We are in a payment business, including payment card, app, and ewallet. We are expert in online payment and Card not present (CNP) transaction.
We need an innovative, modern business card.

Our logo font is Aero Matics

Target Market(s)

Startup - Bank - Online Payment - Card Manufacturing

Industry/Entity Type

Startup

Contact Information for Business Card

phone: 555 014 7396 - Address: 4172 Marlowe blvd, Brenton City, CA 90299

Requirements
Must have
• Message: innovative, professional, expert, high tech, trust, online payment expert, security
Nice to have
• no comment
Should not have
• no Comment

```html
<!DOCTYPE html>
<html lang="en">
<head>
<meta charset="utf-8">
<title>Quorva – Business Card</title>
<link rel="stylesheet" href="https://fonts.googleapis.com/css2?family=Roboto:wght@400;500&display=swap">
<style>
  :root {
    --brand-red: #b51f2e;
    --card-white: #ffffff;
    --backdrop: #1f1f1f;
    --swoosh-grey: #8c8c8c;
    --rule-light: rgba(255,255,255,0.55);
    --text-light: #ffffff;
  }
  * { margin: 0; padding: 0; box-sizing: border-box; }
  html, body {
    width: 1200px; height: 987px; overflow: hidden;
    background: var(--backdrop);
    font-family: "Roboto", Arial, sans-serif;
  }
  .stage { position: relative; width: 1200px; height: 987px; }
  .card {
    position: absolute;
    width: 615px; height: 352px;
    background: var(--card-white);
    overflow: hidden;
  }
  .card--front { left: 293px; top: 130px; }
  .card--back  { left: 292px; top: 505px; }

  .brand { position: absolute; display: flex; align-items: center; }
  .brand__dot { border-radius: 50%; background: var(--brand-red); flex: none; }
  .brand__name {
    color: var(--brand-red);
    font-weight: 500;
    line-height: 1;
    letter-spacing: 1px;
  }
  .card--front .brand { left: 140px; top: 60px; }
  .card--front .brand__dot { width: 100px; height: 100px; margin-right: 16px; }
  .card--front .brand__name { font-size: 66px; }
  .card--back .brand { left: 116px; top: 119px; }
  .card--back .brand__dot { width: 114px; height: 114px; margin-right: 18px; }
  .card--back .brand__name { font-size: 78px; }

  .band { position: absolute; left: 0; top: 0; width: 615px; height: 352px; }

  .contact {
    position: absolute; left: 0; right: 0; top: 254px;
    color: var(--text-light); text-align: center;
  }
  .contact__title {
    display: flex; align-items: center; justify-content: center;
    gap: 8px; font-size: 19px; font-weight: 500;
  }
  .contact__title::before, .contact__title::after {
    content: ""; width: 112px; height: 1px; background: var(--rule-light);
  }
  .contact__role { font-size: 16px; font-weight: 400; }
  .contact__line { font-size: 15px; margin-top: 8px; }
  .contact__line b { font-weight: 500; }
</style>
</head>
<body>
<main class="stage">
  <section class="card card--front">
    <svg class="band" viewBox="0 0 615 352" aria-hidden="true">
      <path d="M0 250 Q307.5 176 615 250 Q307.5 186 0 250 Z" fill="var(--swoosh-grey)"/>
      <path d="M0 253 Q307.5 191 615 253 L615 352 L0 352 Z" fill="var(--brand-red)"/>
    </svg>
    <div class="brand">
      <span class="brand__dot"></span>
      <span class="brand__name">quorva</span>
    </div>
    <div class="contact">
      <p class="contact__title"><span>Marek Ilson - <span class="contact__role">President</span></span></p>
      <p class="contact__line"><b>P :</b> 555 014 7396 <b>E :</b> marek@quorva.com <b>W :</b> www.quorva.com</p>
      <p class="contact__line">4172 Marlowe blvd, Brenton City, CA 90299</p>
    </div>
  </section>

  <section class="card card--back">
    <div class="brand">
      <span class="brand__dot"></span>
      <span class="brand__name">quorva</span>
    </div>
  </section>
</main>
</body>
</html>
```